Im want a website LIKE VRX's and FleetHollow.com's with product payment options like Trenzo's

I need a website LIKE VRX with a header made EXACTLY LIKE THAT OF FLEETHOLLOWS .

The front page photo should be like that of FLEETHOLLOW's webpage as well.

The name of the website will be called "M.K. (Caldera Key)".

We will be targeting ALL MARKETS in a small town in central Panama and charging businesses "listing fees" like a phone book does but also providing informational blogs, news, and other interesting activities.

THIS IS A MULTI PAGE WEBSITE

THIS IS WHERE VRX's website meets Brivelle/FleetHollow.

Once the layout is built I will tweak and modify, add information, and upload items for sale.

Here is a list of specific categories that should be listed out above the front page header image/search bar

-- Home -- News -- Travel -- Activities -- Shop & Dine -- Store -- More... --

These categories should be spread across the bottom of the page in three sections:

WHATS SO GREAT ABOUT (Caldera Key),
HAND PICKED TOURS
ACTIVITIES etc.

Also lets use www.Trenzo.example 's
"HOT DESTINATIONS"
"BEAT THE BEST PRICES IN BOQUETE"
"OCTOBERS INSIDER PICKS"
"TOP DESTINATIONS"
and spread them in four sections side-by-side near the bottom of the page.

Overall I would like to see the finished product to be something LIKE VRX's and FleetHollows.

WE NEED ONLINE PAYMENT OPTIONS LIKE BRIVELLE'S WEBSITE HAS

This will be a desktop website but should be very mobile friendly as well.

-rodmund

P.S. Good luck!

If it isn't already too late to change the website name, the name of the website should be "Caldera Key". Added Friday, October 9, 2015

What do you guys think the budget should be to win this? Added Saturday, October 10, 2015

www.palmorra.example is the most amazing simple site. Whoever can make me a replica with my specifications will win immediately!!!! Added Sunday, October 18, 2015

OMG www.palmorra.example is the bomb!So simple and elegant. Whoever can make me an EXACT REPLICA OF WWW.PALMORRA.EXAMPLE as my site with the specifications mentioned in my brief will take home the $825.00 immediately! Good luck amigos! Added Sunday, October 18, 2015

Does anybody know how to add recurring monthly billing options on this website? Added Sunday, October 18, 2015

ALL MARKETS

Product

Coded - Design and coding required

5+ page

• Coinvey payment options.
• I must be able to add and remove photos/text and video from the HTML files in the page.
• Be creative my friends, and may the odds be forever in your favor!
• I added some photos of a good layout for our page below.

```html
<!DOCTYPE html>
<html lang="en">
<head>
<meta charset="utf-8">
<title>Caldera Key</title>
<link rel="stylesheet" href="https://fonts.googleapis.com/css2?family=Open+Sans:ital,wght@0,300;0,400;0,600;0,700;1,400&family=Noto+Serif:ital,wght@0,700;1,700&display=swap">
<style>
:root{
  --red:#e5564b;
  --red-dark:#c9443a;
  --orange:#f0803c;
  --nav:#3a3a3a;
  --nav-line:#4a4a4a;
  --band:#f3ede9;
  --ink:#444;
  --muted:#9a9a9a;
  --line:#e3e3e3;
  --footer:#2c2c2c;
  --footer-deep:#232323;
  --star:#f2b01e;
  --white:#fff;
}
*{box-sizing:border-box;margin:0;padding:0}
html,body{width:1200px;height:2192px;overflow:hidden}
body{font-family:"Open Sans",Arial,sans-serif;color:var(--ink);background:var(--white);position:relative}
a{color:inherit;text-decoration:none}

/* top bar */
.topbar{height:80px;background:var(--red);display:flex;align-items:center;justify-content:space-between;padding:0 40px 0 48px}
.brand{font-family:"Noto Serif",Georgia,serif;font-weight:700;font-size:34px;color:var(--white)}
.account{display:flex;align-items:center;gap:14px;font-size:13px;color:var(--white)}
.account .link{display:flex;align-items:center;gap:6px}
.select{border:1px solid rgba(255,255,255,.6);padding:4px 10px;border-radius:2px;font-size:12px;display:flex;gap:8px;align-items:center}
.cart{background:var(--white);color:var(--red);padding:6px 12px;border-radius:2px;font-weight:600;font-size:12px;display:flex;gap:6px;align-items:center}

/* nav */
.mainnav{height:44px;background:var(--nav);display:flex;padding-left:48px}
.mainnav a{color:#ddd;font-size:13px;padding:0 18px;line-height:44px;border-right:1px solid var(--nav-line)}
.mainnav a.active{background:var(--red);color:var(--white);font-weight:600}

/* hero */
.hero{position:relative;height:436px;background:linear-gradient(180deg,#6f5b4a 0%,#c89a62 30%,#f0c27a 45%,#b57446 58%,#4b3d38 75%,#2d2a2c 100%);text-align:center}
.hero h1{position:absolute;top:100px;left:0;right:0;font-weight:300;font-size:40px;color:var(--white)}
.finder{position:absolute;top:148px;left:390px;width:420px;background:rgba(40,40,40,.55);border-radius:3px;overflow:hidden}
.finder h2{background:var(--orange);color:var(--white);font-size:19px;font-weight:600;padding:12px 16px;text-align:left}
.finder form{display:flex;gap:8px;padding:16px}
.finder .field{flex:1;height:38px;background:var(--white);border-radius:2px;font-size:12px;color:var(--muted);text-align:left;padding:11px 12px}
.finder .btn{width:90px;height:38px;background:var(--red);color:var(--white);font-size:14px;line-height:38px;border-radius:2px}
.dots{position:absolute;bottom:20px;left:0;right:0;display:flex;justify-content:center;gap:8px}
.dots span{width:9px;height:9px;border-radius:50%;background:rgba(255,255,255,.5)}
.dots span.on{background:var(--white)}

/* services */
.services{height:160px;background:var(--band);display:flex;justify-content:center;gap:40px;padding-top:40px}
.service{width:300px;display:flex;gap:18px}
.service .icon{width:68px;height:68px;border-radius:50%;background:var(--red);flex:none;display:flex;align-items:center;justify-content:center;box-shadow:0 0 0 5px rgba(229,86,75,.25)}
.service h3{color:var(--red);font-size:22px;font-weight:600;margin:6px 0 6px}
.service p{font-size:12px;color:var(--muted);line-height:1.5}

/* listings */
.listings{padding:50px 100px 0}
.section-head{display:flex;align-items:center;gap:16px;margin-bottom:34px}
.section-head h2{color:var(--red);font-size:24px;font-weight:400}
.section-head .rule{flex:1;height:1px;background:var(--line)}
.section-head .dot{width:16px;height:16px;border-radius:50%;background:var(--red)}
.grid{display:grid;grid-template-columns:repeat(4,220px);column-gap:40px;row-gap:30px}
.card{border:1px solid var(--line);padding:8px;height:282px;box-shadow:0 1px 3px rgba(0,0,0,.06)}
.card .photo{height:128px}
.card h4{color:var(--red);font-size:13px;font-weight:600;line-height:1.35;margin:10px 0 5px}
.card .meta{font-size:11px;color:var(--muted)}
.stars{display:flex;gap:2px;margin:6px 0}
.price{display:flex;align-items:baseline;gap:8px}
.price .was{font-size:11px;color:var(--muted);text-decoration:line-through}
.price .now{font-size:22px;color:var(--ink)}

/* register */
.register{position:absolute;top:1480px;left:0;width:1200px;height:400px;background:linear-gradient(160deg,#3f7fae 0%,#2f6e9f 40%,#1f577f 75%,#194766 100%)}
.register-form{position:absolute;left:100px;top:50px;width:400px}
.register-form h2{color:var(--white);font-weight:300;font-size:26px;margin-bottom:22px}
.register-form .row{display:flex;gap:12px;margin-bottom:12px}
.register-form .input{flex:1;height:34px;background:var(--white);font-size:12px;color:var(--muted);padding:9px 10px}
.register-form .area{height:100px}
.register-form .submit{display:inline-block;background:var(--nav);color:var(--white);font-size:13px;padding:9px 18px;margin-top:4px}
.quote{position:absolute;left:620px;top:78px;width:470px;color:var(--white);font-family:"Noto Serif",Georgia,serif;font-style:italic;font-weight:700;font-size:24px;line-height:1.35}
.quote .mark{font-size:52px;line-height:0;vertical-align:-18px;margin-right:6px}
.quote cite{display:block;font-style:normal;font-size:28px;margin-top:12px}

/* contact strip */
.contact{position:absolute;top:1880px;left:0;width:1200px;height:80px;display:flex;align-items:center;padding:0 100px;gap:60px;font-size:12px;color:var(--ink)}
.contact .item{display:flex;align-items:center;gap:8px}
.newsletter{margin-left:auto;display:flex;align-items:center;gap:10px}
.newsletter .field{width:170px;height:28px;border:1px solid var(--line);font-size:11px;color:var(--muted);padding:6px 8px}
.newsletter .go{width:28px;height:28px;background:var(--nav);display:flex;align-items:center;justify-content:center}

/* footer */
.footer{position:absolute;top:1960px;left:0;width:1200px;height:232px;background:var(--footer);padding:30px 100px 0;color:#aaa}
.footer-nav{display:flex;gap:20px;font-size:12px}
.copyright{font-size:12px;margin-top:12px}
.social{position:absolute;right:100px;top:36px;display:flex;gap:8px}
.social span{width:26px;height:26px;background:var(--red);border-radius:2px}
.social span:nth-child(2){background:#5a6f9b}
.social span:nth-child(3){background:#5aa7d8}
.legal{position:absolute;left:0;right:0;bottom:0;height:110px;background:var(--footer-deep);padding:24px 100px;font-size:11px;line-height:1.7;color:#7d7d7d}
</style>
</head>
<body>

<header class="topbar">
  <a class="brand" href="#">Caldera Key</a>
  <div class="account">
    <a class="link" href="#"><svg width="12" height="12" viewBox="0 0 12 12"><rect x="2" y="5" width="8" height="6" fill="#fff"/><path d="M4 5V3.5a2 2 0 0 1 4 0V5" stroke="#fff" fill="none" stroke-width="1.4"/></svg>Login</a>
    <a class="link" href="#"><svg width="12" height="12" viewBox="0 0 12 12"><circle cx="6" cy="4" r="2.5" fill="#fff"/><path d="M1.5 11.5a4.5 4.5 0 0 1 9 0z" fill="#fff"/></svg>Register</a>
    <span class="select">USD $ <svg width="8" height="5"><path d="M0 0h8L4 5z" fill="#fff"/></svg></span>
    <span class="select">English <svg width="8" height="5"><path d="M0 0h8L4 5z" fill="#fff"/></svg></span>
    <a class="cart" href="#"><svg width="13" height="12" viewBox="0 0 13 12"><path d="M0 1h2.5l1.8 7h7l1.5-5H3.4" stroke="#e5564b" fill="none" stroke-width="1.4"/><circle cx="5" cy="10.5" r="1.2" fill="#e5564b"/><circle cx="10" cy="10.5" r="1.2" fill="#e5564b"/></svg>0 item</a>
  </div>
</header>

<nav class="mainnav">
  <a class="active" href="#">Home</a><a href="#">About us</a><a href="#">Tours</a><a href="#">Guides</a><a href="#">Hotels</a><a href="#">Rental Vehicles</a><a href="#">Pricing</a><a href="#">Gallery</a><a href="#">Promotions</a><a href="#">Contact us</a><a href="#">Help</a>
</nav>

<section class="hero" role="img" aria-label="Sunset over the sea with palm silhouettes on the shore">
  <h1>Aenean feugiat viverra lorem ac sagittis</h1>
  <div class="finder">
    <h2>Where you need to go in central Panama</h2>
    <form><span class="field">Enter a destination or keyword</span><span class="btn">Search</span></form>
  </div>
  <div class="dots"><span></span><span class="on"></span><span></span><span></span></div>
</section>

<section class="services">
  <div class="service">
    <span class="icon"><svg width="26" height="32" viewBox="0 0 26 32"><path d="M13 1a11 11 0 0 0-11 11c0 8 11 19 11 19s11-11 11-19A11 11 0 0 0 13 1z" fill="#fff"/><circle cx="13" cy="12" r="4.5" fill="#e5564b"/></svg></span>
    <div><h3>Guided Tours</h3><p>Lorem ipsum dolor sit amet consectetur adipiscing elit sed do eiusmod tempor.</p></div>
  </div>
  <div class="service">
    <span class="icon"><svg width="26" height="30" viewBox="0 0 26 30"><rect x="3" y="2" width="20" height="27" fill="#fff"/><g fill="#e5564b"><rect x="7" y="6" width="4" height="4"/><rect x="15" y="6" width="4" height="4"/><rect x="7" y="13" width="4" height="4"/><rect x="15" y="13" width="4" height="4"/><rect x="10" y="21" width="6" height="8"/></g></svg></span>
    <div><h3>Hotel/Hostels</h3><p>Lorem ipsum dolor sit amet consectetur adipiscing elit sed do eiusmod tempor.</p></div>
  </div>
  <div class="service">
    <span class="icon"><svg width="34" height="22" viewBox="0 0 34 22"><path d="M2 12l4-8h20l5 8v6H2z" fill="#fff"/><circle cx="9" cy="18" r="3.5" fill="#e5564b" stroke="#fff" stroke-width="2"/><circle cx="25" cy="18" r="3.5" fill="#e5564b" stroke="#fff" stroke-width="2"/><path d="M8 11l3-5h5v5zM19 11V6h5l3 5z" fill="#e5564b"/></svg></span>
    <div><h3>Rental Vehicles</h3><p>Lorem ipsum dolor sit amet consectetur adipiscing elit sed do eiusmod tempor.</p></div>
  </div>
</section>

<main class="listings">
  <div class="section-head"><h2>Tour Listings</h2><span class="rule"></span><span class="dot"></span></div>
  <div class="grid">
    <article class="card"><div class="photo" role="img" aria-label="Colonial street with colourful houses" style="background:linear-gradient(160deg,#8fb3d6,#c98a6a 55%,#6d5b52)"></div><h4>Praesent quis risus ut mi mollis sollicitudin</h4><p class="meta">Tellus vestibulum, lorem ipsum</p><div class="stars"><svg width="70" height="12" viewBox="0 0 70 12"><g fill="#f2b01e"><path id="s1" d="M6 0l1.8 3.8 4.2.5-3.1 2.9.8 4.1L6 9.3 2.3 11.3l.8-4.1L0 4.3l4.2-.5z"/><use href="#s1" x="14"/><use href="#s1" x="28"/></g><g fill="#ddd"><use href="#s1" x="42"/><use href="#s1" x="56"/></g></svg></div><div class="price"><span class="was">From $48.9</span><span class="now">421.99</span></div></article>
    <article class="card"><div class="photo" role="img" aria-label="Coastal city skyline by the bay" style="background:linear-gradient(180deg,#9cc4e4,#6f9fc8 50%,#46708f)"></div><h4>Praesent quis risus ut mi mollis sollicitudin</h4><p class="meta">Tellus vestibulum, lorem ipsum</p><div class="stars"><svg width="70" height="12" viewBox="0 0 70 12"><g fill="#f2b01e"><use href="#s1"/><use href="#s1" x="14"/><use href="#s1" x="28"/><use href="#s1" x="42"/></g><use href="#s1" x="56" fill="#ddd"/></svg></div><div class="price"><span class="was">From $48.9</span><span class="now">421.99</span></div></article>
    <article class="card"><div class="photo" role="img" aria-label="City lights at dusk" style="background:linear-gradient(180deg,#2a3f7a,#4a4f9a 50%,#d0704a)"></div><h4>Praesent quis risus ut mi mollis sollicitudin</h4><p class="meta">Tellus vestibulum, lorem ipsum</p><div class="stars"><svg width="70" height="12" viewBox="0 0 70 12"><g fill="#f2b01e"><use href="#s1"/><use href="#s1" x="14"/><use href="#s1" x="28"/></g><g fill="#ddd"><use href="#s1" x="42"/><use href="#s1" x="56"/></g></svg></div><div class="price"><span class="was">From $48.9</span><span class="now">421.99</span></div></article>
    <article class="card"><div class="photo" role="img" aria-label="Green canal with boats" style="background:linear-gradient(180deg,#a9cfe0,#5f9a6a 50%,#3d6a55)"></div><h4>Praesent quis risus ut mi mollis sollicitudin</h4><p class="meta">Tellus vestibulum, lorem ipsum</p><div class="stars"><svg width="70" height="12" viewBox="0 0 70 12"><g fill="#f2b01e"><use href="#s1"/><use href="#s1" x="14"/><use href="#s1" x="28"/><use href="#s1" x="42"/></g><use href="#s1" x="56" fill="#ddd"/></svg></div><div class="price"><span class="was">From $48.9</span><span class="now">421.99</span></div></article>
    <article class="card"><div class="photo" role="img" aria-label="Bridge over the water at sunset" style="background:linear-gradient(180deg,#3e5f86,#8a7d86 50%,#2c3b4d)"></div><h4>Praesent quis risus ut mi mollis sollicitudin</h4><p class="meta">Tellus vestibulum, lorem ipsum</p><div class="stars"><svg width="70" height="12" viewBox="0 0 70 12"><g fill="#f2b01e"><use href="#s1"/><use href="#s1" x="14"/><use href="#s1" x="28"/></g><g fill="#ddd"><use href="#s1" x="42"/><use href="#s1" x="56"/></g></svg></div><div class="price"><span class="was">From $48.9</span><span class="now">421.99</span></div></article>
    <article class="card"><div class="photo" role="img" aria-label="Harbour town under blue sky" style="background:linear-gradient(180deg,#7fb1dc,#cfd9e2 55%,#7b8c99)"></div><h4>Praesent quis risus ut mi mollis sollicitudin</h4><p class="meta">Tellus vestibulum, lorem ipsum</p><div class="stars"><svg width="70" height="12" viewBox="0 0 70 12"><g fill="#f2b01e"><use href="#s1"/><use href="#s1" x="14"/><use href="#s1" x="28"/><use href="#s1" x="42"/></g><use href="#s1" x="56" fill="#ddd"/></svg></div><div class="price"><span class="was">From $48.9</span><span class="now">421.99</span></div></article>
    <article class="card"><div class="photo" role="img" aria-label="Coral reef under clear water" style="background:linear-gradient(180deg,#3fa6c9,#2b7f9e 55%,#1f5a70)"></div><h4>Praesent quis risus ut mi mollis sollicitudin</h4><p class="meta">Tellus vestibulum, lorem ipsum</p><div class="stars"><svg width="70" height="12" viewBox="0 0 70 12"><g fill="#f2b01e"><use href="#s1"/><use href="#s1" x="14"/><use href="#s1" x="28"/></g><g fill="#ddd"><use href="#s1" x="42"/><use href="#s1" x="56"/></g></svg></div><div class="price"><span class="was">From $48.9</span><span class="now">421.99</span></div></article>
    <article class="card"><div class="photo" role="img" aria-label="Tropical island with palm trees" style="background:linear-gradient(180deg,#8ec9e6,#4f9c7a 55%,#2e7f90)"></div><h4>Praesent quis risus ut mi mollis sollicitudin</h4><p class="meta">Tellus vestibulum, lorem ipsum</p><div class="stars"><svg width="70" height="12" viewBox="0 0 70 12"><g fill="#f2b01e"><use href="#s1"/><use href="#s1" x="14"/><use href="#s1" x="28"/><use href="#s1" x="42"/></g><use href="#s1" x="56" fill="#ddd"/></svg></div><div class="price"><span class="was">From $48.9</span><span class="now">421.99</span></div></article>
  </div>
</main>

<section class="register" role="img" aria-label="Underwater scene with a school of fish">
  <div class="register-form">
    <h2>Register for Mileage program</h2>
    <div class="row"><span class="input">Name</span><span class="input">Email</span></div>
    <div class="row"><span class="input">Phone</span><span class="input">Url</span></div>
    <div class="row"><span class="input area">Message</span></div>
    <span class="submit">Submit</span>
  </div>
  <blockquote class="quote"><span class="mark">“</span>Nullam accumsan purus tongue viverra. Mauris suscipit felis id nunc elementum varius elementum nulla <span class="mark">”</span><cite>Darin Moss, NY</cite></blockquote>
</section>

<section class="contact">
  <span class="item"><svg width="12" height="16" viewBox="0 0 12 16"><path d="M6 0a6 6 0 0 0-6 6c0 4.5 6 10 6 10s6-5.5 6-10a6 6 0 0 0-6-6z" fill="#777"/><circle cx="6" cy="6" r="2.2" fill="#fff"/></svg>774 Building name, Street name, City, Zip code</span>
  <span class="item"><svg width="14" height="14" viewBox="0 0 14 14"><path d="M3 0l3 3.5-1.8 1.8a8 8 0 0 0 4.5 4.5L10.5 8 14 11l-2 3C6 14 0 8 0 2z" fill="#777"/></svg>+507 555 0148</span>
  <span class="item"><svg width="16" height="12" viewBox="0 0 16 12"><rect width="16" height="12" fill="#777"/><path d="M0 0l8 6 8-6" stroke="#fff" fill="none" stroke-width="1.2"/></svg>info@calderakey.example</span>
  <div class="newsletter">Newsletter <span class="field">Email</span><span class="go"><svg width="8" height="10"><path d="M0 0l8 5-8 5z" fill="#fff"/></svg></span></div>
</section>

<footer class="footer">
  <nav class="footer-nav"><a href="#">Home</a><a href="#">About us</a><a href="#">Tours</a><a href="#">Guides</a><a href="#">Rental Vehicles</a><a href="#">Pricing</a><a href="#">Gallery</a><a href="#">Testimonials</a><a href="#">Contact us</a><a href="#">Help</a></nav>
  <p class="copyright">Copyright © 2015 Caldera Key. All rights reserved.</p>
  <div class="social"><span></span><span></span><span></span><span></span></div>
  <p class="legal">Caldera Key lists local tours, hotels, hostels and rental vehicles across central Panama. Prices shown are per person and may change with season and availability. Listing fees apply to partner businesses. Read our terms, privacy policy and booking conditions before you pay online. All payments are processed securely.</p>
</footer>

</body>
</html>
```